UI/ UX Design for ERP Software

We need a new UX/UI interface for a ERP software for property managers. Our CMMS / ERP solution is made based on responsive design technologies and is coded in PHP.
The overall UX to be similar to Tev Ulna - easy navigation, intuitive menus.

Industry/Entity Type

Property Management

Number of Pages Required

5+ page

Requirements
Must have
• Round dock buttons
Consistent icons across the application
Enough Spacing between buttons/icons/ menu
Consistent Font
Nice to have
• We would like the UX to allow the users to use the application without /minimum training.
Should not have
• we don't want anything that is classic with respect to UX

```html
<!DOCTYPE html>
<html lang="en">
<head>
<meta charset="utf-8">
<title>Keyvane – Properties list</title>
<link href="https://fonts.googleapis.com/css2?family=Nunito+Sans:wght@400;600;700;800&display=swap" rel="stylesheet">
<style>
:root{
  --bg-top:#f4f8fc;
  --bg-bottom:#dbe9f0;
  --window:#f5f9fc;
  --card:#ffffff;
  --ink:#1c2430;
  --muted:#5b7690;
  --band:#e4f0f9;
  --line:#d6e2ec;
  --blue:#1a8cff;
  --blue-deep:#0b63e5;
  --blue-soft:#cfe5ff;
  --orange:#f26b3a;
  --orange-soft:#f6d2c6;
  --cyan:#04b4f1;
  --cyan-soft:#a9e7fb;
  --yellow:#fbbd42;
  --night:#1f1b2e;
}
*{box-sizing:border-box;margin:0;padding:0}
html,body{width:1200px;height:1200px;overflow:hidden}
body{
  font-family:"Nunito Sans",Arial,sans-serif;
  color:var(--ink);
  background:linear-gradient(180deg,var(--bg-top) 0%,var(--bg-bottom) 100%);
  position:relative;
}
.window{
  position:absolute;left:141px;top:181px;width:918px;height:838px;
  background:var(--window);border-radius:28px;
  box-shadow:0 20px 50px rgba(70,110,140,.12);
}
.abs{position:absolute}
.dots span{position:absolute;top:189px;width:8px;height:8px;border-radius:50%}
.brand{left:179px;top:218px;display:flex;align-items:center;gap:6px;font-weight:800;font-size:14px;color:var(--blue)}
.brand i{width:10px;height:10px;background:var(--blue);border-radius:2px;display:block}
.mode-toggle{left:800px;top:217px;width:55px;height:22px;border:1px solid var(--line);border-radius:11px;background:#fff}
.welcome{left:869px;top:219px;font-size:10.5px}
.welcome b{font-weight:700}
.avatar{left:995px;top:210px;width:34px;height:34px;border-radius:50%;background:linear-gradient(135deg,#6b5a4e,#2d2a2c)}
.page-title{left:175px;top:257px;display:flex;align-items:center;gap:7px;font-size:15.5px;font-weight:600}
.chip{top:296px;width:95px;height:28px;border:1px solid var(--line);border-radius:4px;background:#fff;font-size:8px;font-weight:600;display:flex;align-items:center;justify-content:center}
.tab{top:345px;height:34px;border-radius:4px;display:flex;align-items:center;justify-content:center;gap:6px;font-size:9.5px;font-weight:600}
.tab--active{left:175px;width:141px;background:var(--blue);color:#fff;font-weight:800;box-shadow:0 6px 14px rgba(26,140,255,.25)}
.tab--plain{left:327px;width:160px;background:#fff}
.card{background:var(--card);border-radius:8px}
.stat-title{position:absolute;left:0;right:0;top:15px;text-align:center;font-size:8px;font-weight:800;line-height:1.4}
.pie{position:absolute;left:32px;top:38px}
.legend{position:absolute;left:16px;font-size:8px;font-weight:600;display:flex;align-items:center;gap:8px}
.legend i{width:5px;height:5px;border-radius:50%;display:block}
.legend.muted{color:var(--muted)}
.table-card{left:311px;width:588px;height:120px}
.table-card h2{position:absolute;left:12px;top:15px;font-size:12.5px;font-weight:600}
.table-head{position:absolute;left:11px;right:13px;top:38px;height:23px;background:var(--band);border-radius:2px}
.cell{position:absolute;font-size:9.5px;white-space:nowrap}
.table-head .cell{top:5px;font-weight:600}
.row .cell{color:var(--muted)}
.c1{left:12px}.c2{left:95px}.c3{left:251px}.c4{left:348px}.c5{left:460px}
.row{position:absolute;left:11px;right:13px;height:14px}
.dock{left:527px;top:939px;width:146px;height:56px;background:#fff;border-radius:12px;box-shadow:0 8px 20px rgba(70,110,140,.1)}
.dock-btn{position:absolute;top:8px;width:38px;height:38px;border-radius:10px;display:flex;align-items:center;justify-content:center}
.dock-btn--home{left:21px;background:linear-gradient(180deg,#20a4ff,#0a74f0)}
.dock-btn--apps{left:89px;background:linear-gradient(180deg,#ff8a3a,#f25c28)}
.tooltip{position:absolute;left:33px;top:57px;width:49px;height:17px;background:var(--night);color:#fff;border-radius:3px;font-size:6.5px;font-weight:800;display:flex;align-items:center;justify-content:center}
</style>
</head>
<body>
<div class="window"></div>

<div class="dots">
  <span style="left:175px;background:#fcc53c"></span>
  <span style="left:188px;background:#f04b4b"></span>
  <span style="left:201px;background:#3fcf5f"></span>
</div>

<div class="abs brand"><i></i>Keyvane</div>

<div class="abs mode-toggle">
  <svg width="55" height="22" viewBox="0 0 55 22">
    <circle cx="13" cy="11" r="3.5" fill="var(--yellow)"/>
    <g stroke="var(--yellow)" stroke-width="1.2" stroke-linecap="round">
      <path d="M13 4.5v1.5M13 16v1.5M6.5 11h1.5M18 11h1.5M8.4 6.4l1 1M16.6 14.6l1 1M8.4 15.6l1-1M16.6 7.4l1-1"/>
    </g>
    <circle cx="43" cy="11" r="6.5" fill="#fde7a6" stroke="var(--yellow)" stroke-width="1.5"/>
  </svg>
</div>
<div class="abs welcome">Welcome, <b>Aren Malo</b></div>
<div class="abs avatar" role="img" aria-label="User profile photo"></div>

<h1 class="abs page-title">
  <svg width="23" height="17" viewBox="0 0 23 17" fill="var(--ink)">
    <rect x="0" y="3" width="14" height="14"/><rect x="14" y="7" width="9" height="10"/>
    <g fill="#fff"><rect x="2" y="5" width="2" height="2"/><rect x="6" y="5" width="2" height="2"/><rect x="10" y="5" width="2" height="2"/><rect x="2" y="9" width="2" height="2"/><rect x="6" y="9" width="2" height="2"/><rect x="10" y="9" width="2" height="2"/><rect x="16" y="10" width="2" height="2"/><rect x="19" y="10" width="2" height="2"/></g>
  </svg>
  Properties list
</h1>

<div class="abs chip" style="left:174px">Elm Court</div>
<div class="abs chip" style="left:274px">Elm Court</div>
<div class="abs chip" style="left:374px">Elm Court</div>
<div class="abs chip" style="left:474px">Elm Court</div>
<div class="abs chip" style="left:575px">Elm Court</div>
<div class="abs chip" style="left:675px">Elm Court</div>
<div class="abs chip" style="left:776px">Elm Court</div>

<div class="abs tab tab--active">
  <svg width="9" height="11" viewBox="0 0 9 11"><rect x="0.5" y="1" width="8" height="10" rx="1" fill="#fff"/><g stroke="var(--blue)" stroke-width="1"><path d="M2 4h5M2 6h5M2 8h5"/></g></svg>
  Request / orders
</div>
<div class="abs tab tab--plain">
  <svg width="10" height="10" viewBox="0 0 10 10"><rect x="0" y="1.5" width="10" height="8.5" rx="1" fill="var(--ink)"/><rect x="2" y="0" width="1.5" height="3" fill="var(--ink)"/><rect x="6.5" y="0" width="1.5" height="3" fill="var(--ink)"/><rect x="2" y="5.5" width="2" height="2" fill="#fff"/></svg>
  Maintenance calendar
</div>

<!-- Left stats -->
<section class="abs card" style="left:174px;top:403px;width:122px;height:142px">
  <div class="stat-title">Tenant request by user</div>
  <svg class="pie" width="56" height="56" viewBox="-28 -28 56 56">
    <circle r="27" fill="var(--blue-soft)"/>
    <path d="M0 0L0 -27A27 27 0 0 1 16.6 21.3Z" fill="var(--blue-deep)"/>
  </svg>
  <div class="legend muted" style="top:107px"><i style="background:var(--blue-soft)"></i>No complete (100)</div>
  <div class="legend" style="top:120px"><i style="background:var(--blue-deep)"></i>Completed (65)</div>
</section>

<section class="abs card" style="left:174px;top:561px;width:122px;height:142px">
  <div class="stat-title">Maintenance by user</div>
  <svg class="pie" width="56" height="56" viewBox="-28 -28 56 56">
    <circle r="27" fill="var(--orange-soft)"/>
    <path d="M0 0L0 -27A27 27 0 0 1 16.6 21.3Z" fill="var(--orange)"/>
  </svg>
  <div class="legend muted" style="top:107px"><i style="background:var(--blue-soft)"></i>No complete (100)</div>
  <div class="legend" style="top:120px"><i style="background:var(--orange)"></i>Completed (65)</div>
</section>

<!-- Tables -->
<section class="abs card table-card" style="top:403px">
  <h2>Tenant request</h2>
  <div class="table-head"><span class="cell c1">Ticket ID</span><span class="cell c2">Subject</span><span class="cell c3">Date</span><span class="cell c4">Property</span><span class="cell c5">Tenant</span></div>
  <div class="row" style="top:70px"><span class="cell c1">1232132323</span><span class="cell c2">Request for rent freeze</span><span class="cell c3">01/01/2021</span><span class="cell c4">Elm Court</span><span class="cell c5">Mira Dawson</span></div>
  <div class="row" style="top:91px"><span class="cell c1">1232132323</span><span class="cell c2">Bad neighboors</span><span class="cell c3">01/01/2021</span><span class="cell c4">Elm Court</span><span class="cell c5">Mira Dawson</span></div>
</section>

<section class="abs card table-card" style="top:536px">
  <h2>Maintenance</h2>
  <div class="table-head"><span class="cell c1">Ticket ID</span><span class="cell c2">Subject</span><span class="cell c3">Date</span><span class="cell c4">Property</span><span class="cell c5">Tenant</span></div>
  <div class="row" style="top:70px"><span class="cell c1">1232132323</span><span class="cell c2">Request for rent freeze</span><span class="cell c3">01/01/2021</span><span class="cell c4">Elm Court</span><span class="cell c5">Mira Dawson</span></div>
  <div class="row" style="top:91px"><span class="cell c1">1232132323</span><span class="cell c2">Bad neighboors</span><span class="cell c3">01/01/2021</span><span class="cell c4">Elm Court</span><span class="cell c5">Mira Dawson</span></div>
</section>

<section class="abs card table-card" style="top:665px">
  <h2>Work orders</h2>
  <div class="table-head"><span class="cell c1">Ticket ID</span><span class="cell c2">Subject</span><span class="cell c3">Date</span><span class="cell c4">Property</span><span class="cell c5">Tenant</span></div>
  <div class="row" style="top:70px"><span class="cell c1">1232132323</span><span class="cell c2">Request for rent freeze</span><span class="cell c3">01/01/2021</span><span class="cell c4">Elm Court</span><span class="cell c5">Mira Dawson</span></div>
  <div class="row" style="top:91px"><span class="cell c1">1232132323</span><span class="cell c2">Bad neighboors</span><span class="cell c3">01/01/2021</span><span class="cell c4">Elm Court</span><span class="cell c5">Mira Dawson</span></div>
</section>

<section class="abs card table-card" style="top:793px">
  <h2>Purcharse orders</h2>
  <div class="table-head"><span class="cell c1">Ticket ID</span><span class="cell c2">Subject</span><span class="cell c3">Date</span><span class="cell c4">Property</span><span class="cell c5">Tenant</span></div>
  <div class="row" style="top:70px"><span class="cell c1">1232132323</span><span class="cell c2">Request for rent freeze</span><span class="cell c3">01/01/2021</span><span class="cell c4">Elm Court</span><span class="cell c5">Mira Dawson</span></div>
  <div class="row" style="top:91px"><span class="cell c1">1232132323</span><span class="cell c2">Bad neighboors</span><span class="cell c3">01/01/2021</span><span class="cell c4">Elm Court</span><span class="cell c5">Mira Dawson</span></div>
</section>

<!-- Right stats -->
<section class="abs card" style="left:913px;top:403px;width:122px;height:142px">
  <div class="stat-title">Montly maintenance</div>
  <svg class="pie" width="56" height="56" viewBox="-28 -28 56 56">
    <circle r="27" fill="var(--cyan-soft)"/>
    <path d="M0 0L0 -27A27 27 0 0 1 16.6 21.3Z" fill="var(--cyan)"/>
  </svg>
  <div class="legend muted" style="top:107px"><i style="background:var(--cyan-soft)"></i>No complete (100)</div>
  <div class="legend" style="top:120px"><i style="background:var(--cyan)"></i>Completed (65)</div>
</section>

<section class="abs card" style="left:913px;top:561px;width:122px;height:135px">
  <div class="stat-title">Purcharse orders<br>this week</div>
  <div class="tooltip">8 orders</div>
  <svg class="abs" style="left:0;top:74px" width="122" height="50" viewBox="0 0 122 50">
    <path d="M36 0l4 4 4-4z" fill="var(--night)" transform="translate(13 0)"/>
    <path d="M7 48L18 37 26 42 38 24 45 33 52 20 60 26 76 6 107 48Z" fill="var(--yellow)"/>
    <circle cx="57" cy="23" r="4" fill="#ffd23a" stroke="#f39a1a" stroke-width="1.2"/>
  </svg>
</section>

<!-- Dock -->
<nav class="abs dock">
  <div class="dock-btn dock-btn--home">
    <svg width="22" height="20" viewBox="0 0 22 20"><path d="M11 1L1 10h3v9h5v-6h4v6h5v-9h3z" fill="#fff"/></svg>
  </div>
  <div class="dock-btn dock-btn--apps">
    <svg width="16" height="16" viewBox="0 0 16 16" fill="#fff">
      <circle cx="2.5" cy="2.5" r="1.6"/><circle cx="8" cy="2.5" r="1.6"/><circle cx="13.5" cy="2.5" r="1.6"/>
      <circle cx="2.5" cy="8" r="1.6"/><circle cx="8" cy="8" r="1.6"/><circle cx="13.5" cy="8" r="1.6"/>
      <circle cx="2.5" cy="13.5" r="1.6"/><circle cx="8" cy="13.5" r="1.6"/><circle cx="13.5" cy="13.5" r="1.6"/>
    </svg>
  </div>
</nav>
</body>
</html>
```